redesign of my existing custom website into Wordpress based website

I need someone to redesign my current website into something more classy, simplistic, modern and on trend. I would like it set up on Wordpress in a way thats easy for me to make my own additions to blogs/price changes and promotion banners. I will also need a page that is password protected so members can login and have access to all my training videos and resources.
website is www.tidewellmamas.com.au

Target Market(s)

new mums

Industry/Entity Type

Fitness

Coding

Coded - Design and coding required

Number of Pages Required

5+ page

Colors
33a6d7

Requirements
Must have
• chic, modern, stylish and simplistic.
• a call to action above the page fold
• mobile friendly conversion
• a pop up message as soon as someone enters my sight offering my free report
• a members page that is password protected containing 3 youtube videos and 6 pdf attachments as resources
• a home page
• a contact us page
• an about us page
• a blog page
• a store page
Nice to have
• some examples of my peers websites that I like:
• www.norapellwick.com
• https://www.9qlr.com
• https://41bytedgarth.com
Should not have
• anything gimmicky

```html
<!DOCTYPE html>
<html lang="en">
<head>
<meta charset="utf-8">
<title>Tidewell Mamas – 12 Week Home Workout Program For Mums</title>
<link href="https://fonts.googleapis.com/css2?family=Nunito+Sans:wght@300;400;600;700;800&display=swap" rel="stylesheet">
<style>
:root{
  --brand:#33a6d7;
  --brand-dark:#2a8fc0;
  --brand-deep:#1f6f9e;
  --pink:#c4216c;
  --ink:#1b1b1b;
  --text:#555;
  --muted:#8a8a8a;
  --light:#f4f4f4;
  --dark:#2b2b2b;
  --white:#fff;
  --line:#e3e3e3;
}
*{margin:0;padding:0;box-sizing:border-box}
html,body{width:1200px;height:4225px;overflow:hidden}
body{font-family:"Nunito Sans",Arial,sans-serif;color:var(--text);background:var(--white);position:relative}
.abs{position:absolute}
.btn{position:absolute;display:flex;align-items:center;justify-content:center;font-weight:700;text-transform:uppercase;letter-spacing:.5px;border-radius:3px}
.btn--brand{background:var(--brand);color:var(--white)}
.btn--white{background:var(--white);color:var(--brand)}
.center{left:0;width:1200px;text-align:center}

/* hero */
.hero{position:absolute;left:0;top:0;width:1200px;height:797px;overflow:hidden}
.hero__photo{position:absolute;inset:0;background:linear-gradient(180deg,#5d5d5d 0%,#7a7775 40%,#8b8580 70%,#6c6560 100%)}
.hero__shade{position:absolute;inset:0;background:rgba(20,20,20,.35)}
.logo{position:absolute;border-radius:50%;background:var(--white);display:flex;align-items:center;justify-content:center;text-align:center;color:var(--pink);font-weight:700;line-height:1.1}
.hero .logo{left:188px;top:18px;width:116px;height:116px;font-size:17px}
.nav{position:absolute;top:58px;left:518px;display:flex;gap:0}
.nav a{color:var(--white);font-size:15px;font-weight:700;text-decoration:none;margin-right:47px;padding-bottom:6px}
.nav a.is-active{border-bottom:2px solid var(--white)}
.hero__title{top:358px;color:var(--white);font-size:29px;font-weight:300;line-height:38px}
.hero__cta{left:473px;top:465px;width:254px;height:65px;font-size:21px}
.dots{position:absolute;display:flex;gap:10px}
.dots span{width:7px;height:7px;border-radius:50%;background:rgba(255,255,255,.55)}
.dots span.on{background:var(--brand)}

/* promo split */
.promo{position:absolute;top:797px;left:0;width:1200px;height:550px}
.promo__left{position:absolute;left:0;top:0;width:598px;height:550px;background:linear-gradient(160deg,#3aa9da 0%,#2c8fc2 60%,#2784b8 100%)}
.promo__right{position:absolute;left:598px;top:0;width:602px;height:550px;background:var(--light)}
.promo__headline{left:127px;top:58px;color:var(--white);font-size:42px;font-weight:700;line-height:47px}
.promo__from{left:127px;top:262px;color:var(--white);font-size:24px;font-weight:700}
.promo__price{left:127px;top:290px;color:var(--white);font-size:48px;font-weight:300}
.promo__price b{font-weight:800}
.promo__cta{left:127px;top:425px;width:231px;height:62px;font-size:20px}
.optin__title{left:620px;top:62px;color:var(--ink);font-size:41px;font-weight:800;line-height:48px}
.optin__sub{left:620px;top:175px;color:#444;font-size:18px;line-height:26px}
.field{position:absolute;left:620px;width:445px;height:56px;background:var(--white);border:1px solid var(--line);font-size:14px;color:#aaa;padding-left:26px;display:flex;align-items:center}
.optin__cta{left:620px;top:423px;width:231px;height:62px;font-size:18px}

/* testimonial */
.story__photo{position:absolute;width:164px;height:164px;border-radius:50%;border:4px solid var(--brand);background:radial-gradient(circle at 50% 40%,#c9a58a 0%,#8d6d5a 55%,#5e86a3 100%)}
.story__label{position:absolute;top:1725px;width:164px;text-align:center;font-size:14px;color:#444}
.story__name{top:1760px;color:var(--brand);font-size:32px;font-weight:700}
.story__role{top:1798px;font-size:20px;color:#444}
.story__stat{top:1832px;font-size:12px;color:#333}
.story__quote{left:160px;top:1884px;width:882px;text-align:center;font-size:15px;line-height:28px;color:#333}
.dots--blue span{background:#c8c8c8}

/* included */
.included{position:absolute;top:2104px;left:0;width:1200px;height:412px;background:linear-gradient(180deg,#2f2f2f,#262626)}
.included__h{color:var(--brand);font-size:33px;font-weight:700}
.included__sub{color:#eee;font-size:20px}
.included__small{color:#ddd;font-size:12px}
.included__rule{left:501px;top:2326px;width:192px;height:3px;background:var(--white)}
.included__body{left:250px;width:700px;text-align:center;color:#ddd;font-size:12.5px;line-height:22px}

.price-band{position:absolute;top:2516px;left:0;width:1200px;height:138px;background:linear-gradient(90deg,#2a8fc0,#33a6d7 50%,#2a8fc0)}
.price-band__main{top:34px;color:var(--white);font-size:36px;font-weight:700}
.price-band__sub{top:82px;color:var(--white);font-size:28px;font-weight:300}

/* features */
.features__h{top:2718px;color:var(--ink);font-size:36px;font-weight:700}
.feature__icon{position:absolute;width:56px;height:56px}
.feature__title{position:absolute;color:var(--brand);font-size:21px;font-weight:700;line-height:25px}
.feature__body{position:absolute;width:455px;font-size:12px;line-height:25.5px;color:#888}
.feature__more{width:102px;height:30px;font-size:11px;text-transform:none}

/* cta */
.cta{position:absolute;top:3479px;left:0;width:1200px;height:375px;background:linear-gradient(180deg,#3ca8d8 0%,#2b8fc4 100%)}
.cta__title{top:142px;color:var(--white);font-size:31px;font-weight:700;line-height:38px}
.cta__btn{left:485px;top:256px;width:230px;height:57px;font-size:20px}

/* footer */
.footer .logo{left:147px;top:3930px;width:112px;height:112px;border:1px solid var(--line);font-size:16px}
.footer h4{position:absolute;top:3932px;color:var(--brand);font-size:15px;font-weight:700}
.footer__about{left:276px;top:3978px;width:240px;font-size:12px;line-height:24px;color:#444}
.footer ul{position:absolute;top:3976px;list-style:none;font-size:12px;line-height:24px;color:#444}
.social{position:absolute;top:3984px;width:12px;height:12px;border-radius:50%;background:var(--brand)}
.footer__bar{position:absolute;top:4164px;left:0;width:1200px;height:61px;border-top:1px solid var(--line);text-align:center;font-size:12px;line-height:61px;color:#444}
</style>
</head>
<body>

<header class="hero">
  <div class="hero__photo" role="img" aria-label="Photo of a smiling mum exercising with a dumbbell at home while her toddler plays beside her"></div>
  <div class="hero__shade"></div>
  <div class="logo">Tidewell<br>Mamas</div>
  <nav class="nav">
    <a class="is-active">Home</a><a>About Us</a><a>Program</a><a>Blog</a><a>Shop</a><a>Contact Us</a>
  </nav>
  <p class="abs center hero__title">Lose your baby weight and Bounce Back into shape!<br>12 week Home Workout Program For Mums!</p>
  <a class="btn btn--brand hero__cta">Get Started</a>
  <div class="dots" style="left:572px;top:704px"><span class="on"></span><span></span><span></span><span></span></div>
</header>

<section class="promo">
  <div class="promo__left" role="img" aria-label="Blue-tinted photo of a mum working out"></div>
  <div class="promo__right"></div>
  <h2 class="abs promo__headline">Start seeing<br>amazing results<br>in just a few weeks!</h2>
  <p class="abs promo__from">Starting from</p>
  <p class="abs promo__price">only <b>$7.50/Week!</b></p>
  <a class="btn btn--white promo__cta">Get Started</a>
  <div class="optin">
    <h2 class="abs optin__title">Get your FREE top 10<br>Baby Belly Blasting Tips</h2>
    <p class="abs optin__sub">See our secret tips to a flatter yummy mummy tummy<br>that you can start implementing for free today!</p>
    <div class="field" style="top:251px">Enter Your Name</div>
    <div class="field" style="top:330px">Enter Your E-mail</div>
    <a class="btn btn--brand optin__cta">Get it Free Now !</a>
  </div>
</section>

<section class="story">
  <div class="story__photo" style="left:419px;top:1549px" role="img" aria-label="Before photo of the founder"></div>
  <div class="story__photo" style="left:617px;top:1549px" role="img" aria-label="After photo of the founder"></div>
  <p class="story__label" style="left:419px">Before</p>
  <p class="story__label" style="left:617px">After</p>
  <p class="abs center story__name">Marla</p>
  <p class="abs center story__role">Tidewell Mamas Founder</p>
  <p class="abs center story__stat">Lost 12 kgs and 25 cms in 12 weeks!</p>
  <p class="abs story__quote">“After spending a lot of time researching the best post pregnancy training methods, I created this program to help me get back into shape after my second baby. In just 12 weeks using this program I was back to my pre baby body and feeling amazing! Now I’m on a mission to share my secrets with other mums so they can achieve awesome results too.”</p>
  <div class="dots dots--blue" style="left:563px;top:2022px"><span class="on"></span><span></span><span></span><span></span></div>
</section>

<section class="included" role="img" aria-label="Dark photo backdrop of workout equipment"></section>
<h2 class="abs center included__h" style="top:2170px">What's included in the program?</h2>
<p class="abs center included__sub" style="top:2232px">12 week Home Workout Program - Equipment Pack</p>
<p class="abs center included__small" style="top:2263px">Your purchase of the Home Workout Program - Equipment Pack comes loaded with value including:</p>
<div class="abs included__rule"></div>
<h2 class="abs center included__h" style="top:2352px">Our unique 3 stage, 12 week training program</h2>
<p class="abs included__body" style="top:2403px">Gradually build back your fitness and core strength and also lose baby weight with our training circuit and fitness program. We take you through 3 workout programs that increase with intensity and are designed for new mums as well as experienced mums.</p>

<section class="price-band">
  <p class="abs center price-band__main">One time only payment of $199 *including GST</p>
  <p class="abs center price-band__sub">That's only $16.60 per week!</p>
  <svg class="abs" style="left:88px;top:57px" width="16" height="24" viewBox="0 0 16 24"><path d="M13 2 3 12l10 10" fill="none" stroke="#111" stroke-width="4"/></svg>
  <svg class="abs" style="left:1096px;top:57px" width="16" height="24" viewBox="0 0 16 24"><path d="m3 2 10 10L3 22" fill="none" stroke="#111" stroke-width="4"/></svg>
</section>

<section class="features">
  <h2 class="abs center features__h">Why our program is different ?</h2>

  <div class="feature">
    <svg class="feature__icon" style="left:146px;top:2842px" viewBox="0 0 56 56" fill="none" stroke="#222" stroke-width="3"><circle cx="28" cy="31" r="17"/><path d="M28 31V21M23 8h10M28 8v6"/></svg>
    <h3 class="feature__title" style="left:220px;top:2852px">Specially Designed For Mums</h3>
    <p class="feature__body" style="left:146px;top:2918px">Unlike other home workout programs out there ours is designed specially for mums. Because our bodies go through such a major change during pregnancy so should the way in which we train afterwards in order to achieve the best results. Our programs have a very large focus on functional training methods</p>
    <a class="btn btn--brand feature__more" style="left:146px;top:3053px">Read More</a>
  </div>

  <div class="feature">
    <svg class="feature__icon" style="left:612px;top:2842px" viewBox="0 0 56 56" fill="none" stroke="#222" stroke-width="3"><path d="M28 48 8 28a11 11 0 0 1 20-14 11 11 0 0 1 20 14z"/><path d="M19 28h18M19 24v8M37 24v8"/></svg>
    <h3 class="feature__title" style="left:687px;top:2840px">Workout Equipment Included<br>So You Can Train From Home</h3>
    <p class="feature__body" style="left:612px;top:2918px">Unlike other home workout programs out there ours is designed specially for mums. Because our bodies go through such a major change during pregnancy so should the way in which we train afterwards in order to achieve the best results. Our programs have a very large focus on functional training methods</p>
    <a class="btn btn--brand feature__more" style="left:612px;top:3053px">Read More</a>
  </div>

  <div class="feature">
    <svg class="feature__icon" style="left:146px;top:3130px" viewBox="0 0 56 56" fill="none" stroke="#222" stroke-width="3"><rect x="14" y="16" width="28" height="32" rx="5"/><path d="M18 8h20v8H18zM20 30h16"/></svg>
    <h3 class="feature__title" style="left:220px;top:3140px">Delicious Low Fat Family<br>Friendly Recipes</h3>
    <p class="feature__body" style="left:146px;top:3205px">Unlike other home workout programs out there ours is designed specially for mums. Because our bodies go through such a major change during pregnancy so should the way in which we train afterwards in order to achieve the best results. Our programs have a very large focus on functional training methods</p>
    <a class="btn btn--brand feature__more" style="left:146px;top:3349px">Read More</a>
  </div>

  <div class="feature">
    <svg class="feature__icon" style="left:612px;top:3130px" viewBox="0 0 56 56" fill="none" stroke="#222" stroke-width="3"><path d="M18 4l8 16M38 4l-8 16"/><circle cx="28" cy="34" r="15"/><path d="m28 26 2.5 5 5 .7-3.6 3.5.9 5-4.8-2.5-4.8 2.5.9-5-3.6-3.5 5-.7z"/></svg>
    <h3 class="feature__title" style="left:687px;top:3140px">Cates For Mums At All Stages Of<br>Post Baby Recovery</h3>
    <p class="feature__body" style="left:612px;top:3205px">Unlike other home workout programs out there ours is designed specially for mums. Because our bodies go through such a major change during pregnancy so should the way in which we train afterwards in order to achieve the best results. Our programs have a very large focus on functional training methods</p>
    <a class="btn btn--brand feature__more" style="left:612px;top:3349px">Read More</a>
  </div>
</section>

<section class="cta" role="img" aria-label="Blue-tinted photo of a happy mum relaxing on a couch">
  <p class="abs center cta__title">Take the first step today by joining our program<br>and let us help you bounce back to the body that you deserve!</p>
  <a class="btn btn--white cta__btn">Get Started</a>
</section>

<footer class="footer">
  <div class="logo">Tidewell<br>Mamas</div>
  <h4 style="left:276px">About Us</h4>
  <p class="abs footer__about">Before you begin any type of exercise post baby, you must ensure you get the ok from your doctor or obstetrician.Its essential you give your body the appropriate amount of time to fully recover before attempting any form of exercise</p>
  <h4 style="left:620px">Quick Links</h4>
  <ul style="left:620px"><li>Home</li><li>About Us</li><li>Programs</li><li>Blog</li><li>Shop</li><li>Contact</li></ul>
  <h4 style="left:766px">Other Links</h4>
  <ul style="left:766px"><li>Terms Of Service</li><li>Privacy Policy</li><li>Help</li><li>Disclaimer</li></ul>
  <h4 style="left:921px">Connect With Us</h4>
  <span class="social" style="left:923px"></span>
  <span class="social" style="left:942px"></span>
  <p class="footer__bar">© 2017 Company Name | All Rights Reserved</p>
</footer>

</body>
</html>
```